Business card design Needed for new logo / Construction business, home extensions and new builds

We need a business card design using our new logo files which i will attach to this project :)

We are a small construction business specialising in home extensions, new builds and property development. We are very ambitious and would appreciate professional and elegant designs for our new business card.

Very serious about using the services on MakerQuarry and recently acquired our new logo from here :)

Please get involved, i will feedback when i can as i am very busy but can respond daily, thanks

Target Market(s)

People that want to build onto their houses, new building developments or adding too their existing property

Industry/Entity Type

Construction

Contact Information for Business Card

Renwick Tolliver Construction, Lionel Ashby (Managing Director), Tel 07822254961, email - info@renwick-tolliver, www.renwick-tolliver.co.uk

Colors

Designer to choose colors to be used in the design.

Requirements
Must have
• I like a deep grey on the back please. A lot of you have provided black from and back, try mixing things up a little. The black looks cool 😎 Thanks

```html
<!DOCTYPE html>
<html lang="en">
<head>
<meta charset="utf-8">
<title>Renwick Tolliver Construction – Business Card</title>
<link rel="stylesheet" href="https://fonts.googleapis.com/css2?family=Open+Sans:wght@400;600;700&display=swap">
<style>
  :root {
    --stage: #242424;
    --card: #1f1f23;
    --card-back: #2a2a2e;
    --gold: #e7b52c;
    --gold-deep: #c98f1c;
    --silver: #d9d9dc;
    --text: #f4f4f4;
    --back-mark: #5c5c64;
    --icon-ink: #1f1f23;
  }
  * { box-sizing: border-box; margin: 0; padding: 0; }
  html, body {
    width: 1200px; height: 780px; overflow: hidden;
    background: var(--stage);
    font-family: "Open Sans", Arial, sans-serif;
  }
  .stage {
    position: relative; width: 1200px; height: 780px;
    display: flex; justify-content: center; align-items: center; gap: 60px;
  }
  .card {
    position: relative; width: 360px; height: 610px;
    border-radius: 22px;
    border: 3px solid var(--gold);
    background: var(--card);
    overflow: hidden;
  }
  .card--back { background: var(--card-back); display: flex; align-items: center; justify-content: center; }
  .back-mark {
    color: var(--back-mark);
    font-weight: 700; font-size: 26px; letter-spacing: 3px;
    text-transform: uppercase; text-align: center; line-height: 1.35;
  }
  .brand {
    position: absolute; top: 78px; left: 0; right: 0;
    text-align: center; color: var(--gold);
    font-weight: 600; font-size: 21px; letter-spacing: 3px;
    text-transform: uppercase; line-height: 1.4;
  }
  .person { position: absolute; top: 268px; left: 0; right: 0; text-align: center; }
  .person__name { font-weight: 700; font-size: 32px; line-height: 1.1; }
  .person__first { color: var(--silver); }
  .person__last { color: var(--gold); }
  .person__role { color: var(--text); font-size: 14px; font-weight: 600; margin-top: 4px; }
  .divider {
    display: block; width: 280px; height: 2px; margin: 16px auto 0;
    background: var(--gold); border: 0;
  }
  .icons { display: flex; justify-content: center; gap: 10px; margin-top: 12px; }
  .contact { color: var(--text); font-size: 15px; line-height: 1.45; margin-top: 8px; }
  .address { color: var(--text); font-size: 15px; line-height: 1.45; margin-top: 8px; }
</style>
</head>
<body>
<main class="stage">
  <section class="card card--back" aria-label="Card back">
    <p class="back-mark">Renwick Tolliver<br>Construction</p>
  </section>

  <section class="card card--front" aria-label="Card front">
    <p class="brand">Renwick Tolliver<br>Construction</p>

    <div class="person">
      <h1 class="person__name"><span class="person__first">Lionel</span> <span class="person__last">Ashby</span></h1>
      <p class="person__role">Managing Director</p>

      <hr class="divider">

      <div class="icons" aria-hidden="true">
        <svg width="26" height="26" viewBox="0 0 26 26"><circle cx="13" cy="13" r="13" fill="var(--gold)"/><path d="M9 7l3 3-1.5 2a8 8 0 0 0 3.5 3.5l2-1.5 3 3-2 2c-5 0-10-5-10-10z" fill="var(--icon-ink)"/></svg>
        <svg width="26" height="26" viewBox="0 0 26 26"><circle cx="13" cy="13" r="13" fill="var(--gold)"/><rect x="7" y="9" width="12" height="9" fill="none" stroke="var(--icon-ink)" stroke-width="1.6"/><path d="M7 9l6 5 6-5" fill="none" stroke="var(--icon-ink)" stroke-width="1.6"/></svg>
        <svg width="26" height="26" viewBox="0 0 26 26"><circle cx="13" cy="13" r="13" fill="var(--gold)"/><circle cx="13" cy="13" r="6.5" fill="none" stroke="var(--icon-ink)" stroke-width="1.5"/><ellipse cx="13" cy="13" rx="2.8" ry="6.5" fill="none" stroke="var(--icon-ink)" stroke-width="1.3"/><path d="M6.5 13h13" stroke="var(--icon-ink)" stroke-width="1.3"/></svg>
      </div>

      <p class="contact">0782 225 4961<br>info@renwick-tolliver.co.uk<br>www.renwick-tolliver.co.uk</p>

      <hr class="divider">

      <div class="icons" aria-hidden="true">
        <svg width="26" height="26" viewBox="0 0 26 26"><circle cx="13" cy="13" r="13" fill="var(--gold)"/><path d="M13 6a5 5 0 0 0-5 5c0 4 5 9 5 9s5-5 5-9a5 5 0 0 0-5-5z" fill="var(--icon-ink)"/><circle cx="13" cy="11" r="2" fill="var(--gold)"/></svg>
      </div>

      <p class="address">Hollin Lane, Westmere<br>Ashcombe, AC4 7RT</p>
    </div>
  </section>
</main>
</body>
</html>
```